TALMORK

The business want a professional looking business card. We have a scetch we will add but want the extra upgrade, and would like more suggestions for variations of our business cards.

```html
<!DOCTYPE html>
<html lang="en">
<head>
<meta charset="utf-8">
<title>TALMORK – Business Cards</title>
<link rel="stylesheet" href="https://fonts.googleapis.com/css2?family=Playfair+Display:wght@700&family=Montserrat:wght@400;500&display=swap">
<style>
  :root {
    --page-bg: #2a2a2c;
    --card-black: #121212;
    --card-edge: #050505;
    --gold: #d9a82e;
    --gold-soft: #c8961f;
    --ink-light: #f1f1f1;
    --emboss: #3a3a3a;
    --emboss-light: #4a4a4a;
  }
  * { margin: 0; padding: 0; box-sizing: border-box; }
  html, body { width: 1200px; height: 900px; overflow: hidden; }
  body { background: var(--page-bg); position: relative; font-family: "Montserrat", sans-serif; }

  .card {
    position: absolute;
    width: 560px;
    height: 320px;
    border-radius: 26px;
    background: var(--card-black);
    box-shadow: 0 4px 0 var(--card-edge), 0 8px 0 var(--card-edge), 0 20px 40px rgba(0,0,0,.55);
    overflow: hidden;
  }

  /* Front: contact side */
  .card-front { left: 580px; top: 90px; }
  .brand {
    position: absolute;
    left: 200px; top: 34px;
    text-align: center;
  }
  .brand-name {
    font-family: "Playfair Display", serif;
    font-weight: 700;
    font-size: 44px;
    letter-spacing: 6px;
    color: var(--gold);
    line-height: 1;
  }
  .brand-tagline {
    font-family: "Montserrat", sans-serif;
    font-size: 10px;
    letter-spacing: 7px;
    color: var(--gold);
    margin-top: 6px;
  }
  .person { position: absolute; left: 40px; top: 118px; }
  .person-name {
    font-family: "Playfair Display", serif;
    font-weight: 700;
    font-size: 26px;
    color: var(--gold);
  }
  .person-role { font-size: 13px; color: var(--ink-light); margin-top: 4px; }
  .contacts { position: absolute; left: 40px; top: 204px; list-style: none; }
  .contacts li {
    display: flex; align-items: center; gap: 10px;
    font-size: 13px; color: var(--ink-light);
    margin-bottom: 9px;
  }
  .contacts svg { width: 13px; height: 13px; fill: var(--gold); flex: none; }
  .brand-dot {
    position: absolute;
    right: 40px; top: 130px;
    width: 150px; height: 150px;
    border-radius: 50%;
    background: var(--gold-soft);
  }

  /* Back: brand side */
  .card-back { left: 60px; top: 480px; }
  .back-lockup {
    position: absolute; inset: 0;
    display: flex; flex-direction: column; align-items: center; justify-content: center;
  }
  .back-dot {
    width: 64px; height: 64px; border-radius: 50%;
    background: var(--emboss-light);
    margin-bottom: 18px;
  }
  .back-name {
    font-family: "Playfair Display", serif;
    font-weight: 700;
    font-size: 50px;
    letter-spacing: 7px;
    color: var(--emboss);
    line-height: 1;
  }
  .back-tagline {
    font-size: 11px;
    letter-spacing: 8px;
    color: var(--emboss);
    margin-top: 10px;
  }
</style>
</head>
<body>

<section class="card card-front">
  <div class="brand">
    <div class="brand-name">TALMORK</div>
    <div class="brand-tagline">SINCE 2026</div>
  </div>
  <div class="person">
    <div class="person-name">Lars Henrik Voldmo</div>
    <div class="person-role">CEO &amp; Founder</div>
  </div>
  <ul class="contacts">
    <li>
      <svg viewBox="0 0 24 24"><path d="M6.6 10.8a15.1 15.1 0 0 0 6.6 6.6l2.2-2.2c.3-.3.7-.4 1-.2 1.1.4 2.3.6 3.6.6.6 0 1 .4 1 1V20c0 .6-.4 1-1 1A17 17 0 0 1 3 4c0-.6.4-1 1-1h3.5c.6 0 1 .4 1 1 0 1.3.2 2.5.6 3.6.1.3 0 .7-.2 1z"/></svg>
      004790415527
    </li>
    <li>
      <svg viewBox="0 0 24 24"><path d="M3 5h18v14H3z M3 5l9 7 9-7" stroke="#121212" stroke-width="1.6"/></svg>
      talmork.studio@mail.com
    </li>
    <li>
      <svg viewBox="0 0 24 24"><circle cx="12" cy="12" r="10"/><path d="M2 12h20M12 2c3 3 3 17 0 20M12 2c-3 3-3 17 0 20" stroke="#121212" stroke-width="1.4" fill="none"/></svg>
      www.talmork.co
    </li>
  </ul>
  <div class="brand-dot"></div>
</section>

<section class="card card-back">
  <div class="back-lockup">
    <div class="back-dot"></div>
    <div class="back-name">TALMORK</div>
    <div class="back-tagline">SINCE 2026</div>
  </div>
</section>

</body>
</html>
```